Wordpress Theme for Brevacare Clinics

** Please view updated Sitemap2.pdf doc to clarify some confusion ***

This is a multiuser WordPress subscription site for Brevacare Clinics. Please see attachment for sitemap. Please do not include extra content like social media icons, search bars, or images. If you have questions, please ask for clarification.
The site contains the following pages and sub-pages:

1. Home
2. Our Clinic
2a. Our Clinic > Mission
2b. Our Clinic > Services
2c. Our Clinic > Clinic Policies
2d. Our Clinic > Schedules
3. Our Staff
3a. Our Staff > [Staff member page]
4. Resources
4a. Resources > Patient Health (index)
4b. Resources > Patient Health (index) > [post]
4c. Resources > Links
4d. Resources > Forms
5. Alerts
5a. Alerts > [Alert Page]
6. Contact Us

Includes the Following Pages, Subpages, and Content
1. Home
a. About Us
b. Our Staff
c. Bulletins
d. Accepting New Patients (shown as an alert widget)
e. Links
i. Physician Toolbox
ii. Book an Appointment
f. Clinic Policies
i. Show first 3 policies (e.g. Late Arrivals, Missed Appointments, Fees)
ii. Link to Clinic Policies page
g. Primary widget (displayed on all pages)
i. Hours of operation
ii. Contact Info
1. Tel
2. Fax
3. Email
4. Address
5. Get directions (link to Google Maps)
2. Our Clinic
a. Main Page
i. Clinic Name
ii. Overview
iii. Languages Spoken
iv. Secondary Navigation
1. Mission
2. Services
3. Clinic Policies
4. Schedules (see attachment)
b. Our Clinic > Mission
c. Our Clinic > Services
i. For each service include service TITLE and DESCRIPTION
d. Our Clinic > Clinic Policies
i. For each policy include policy TITLE and DESCRIPTION
ii. Include the following policies in mockup
1. Late arrivals
2. Missed appointments
3. Fees for missed appointments
4. Referrals and follow-ups
5. Services not covered by RDA
6. Information for LTF patients
7. Medical Legal Reports
e. Our Clinic > Schedules
3. Our Staff
a. Main Page
i. Display a list of staff members. Include NAME and DESIGNATION
b. Our Staff > [Staff Name]
i. Include NAME, PICTURE, DESIGNATION, and BIO
4. Resources
a. Resources > Patient Health
i. Main Page
1. Posts (ordered by date)
a. Title
b. Summary
2. Side Navigation
a. Post Categories
ii. Patient Health > [post title]
1. Title
2. Post Category
3. Date
4. Author
5. Summary
6. Body
b. Resources > Links
1. Secondary Navigation - Categories
a. Sample Categories:
i. Local Services
ii. RDA and Drug Coverage
iii. Mental Health Resources
2. Category page
a. Include the following links in the 'Local Services' category
i. Hypertension clinics
ii. Home Care services
iii. Vaccine Clinics
c. Resources > Forms
i. Display a table with form TITLE and CATEGORY
ii. Side Navigation
1. Form Categories
a. Use the following sample Categories
i. Referrals
ii. Insurance
iii. Intake
iv. Discharge
v. Waivers
5. Alerts
a. Main page
i. List of all Alert posts
1. Include post TITLE as a link to the post
ii. Side Navigation
1. Alerts Archive
a. shown as Month + Number of posts
iii. Alerts > [Alert page]
1. Include TITLE, DATE, AUTHOR, BODY
6. Contact Us
a. Map
b. Hours of operation
c. Address
d. Phone number
e. Fax number
e. Fax number
f. Map
g. Email

Design notes:
- fixed width
- responsive (need designs for mobile, tablet, and desktop)
- simple, dark font, white background
- use Font Awesome icons where needed
- user adds own logo

Target Market(s)

Brevacare Clinics

Industry/Entity Type

Medical

Number of Pages Required

5+ page

Font styles to use
Serif
Sans Serif

Requirements
Must have
• Please keep designs very simple.
• Examples:
• https://www.quolbin.com/install
• http://www.ventrohax.com/company/about-us
• http://brindlequota.org/
• http://www.trosk.com/
Should not have
• Minimal or no use of shadows and gradients

```html
<!DOCTYPE html>
<html lang="en">
<head>
<meta charset="utf-8">
<title>Brevacare Clinics – Policies</title>
<link href="https://fonts.googleapis.com/css2?family=Open+Sans:wght@400;600;700&display=swap" rel="stylesheet">
<style>
:root{
  --blue:#0a8fe2;
  --ink:#2b2b2b;
  --text:#333;
  --rule:#dcdcdc;
  --band:#f7f7f7;
  --footer:#282828;
  --footer-text:#8a8a8a;
  --footer-head:#9a9a9a;
  --white:#fff;
}
*{box-sizing:border-box;margin:0;padding:0}
html,body{width:1150px;height:1200px;overflow:hidden}
body{position:relative;font-family:"Open Sans",Arial,sans-serif;color:var(--text);background:var(--white)}
a{color:inherit;text-decoration:none}

.topbar{position:absolute;left:0;top:0;width:1150px;height:29px;background:var(--blue);color:var(--white);font-size:9px;font-weight:600}
.topbar .help{position:absolute;left:155px;top:8px}
.topbar .help span+span{border-left:1px solid var(--white);margin-left:5px;padding-left:4px}
.topbar .quick{position:absolute;right:155px;top:8px}
.topbar .quick a+a{border-left:1px solid var(--white);margin-left:5px;padding-left:6px}

.header{position:absolute;left:0;top:29px;width:1150px;height:79px}
.brand{position:absolute;left:155px;top:24px;display:flex;align-items:center;gap:10px;font-size:20px;font-weight:600;color:var(--ink);white-space:nowrap}
.brand .dot{width:14px;height:14px;border-radius:50%;background:var(--blue)}
.mainnav{position:absolute;left:0;top:0;height:79px;font-size:10.5px;color:var(--ink)}
.mainnav a{position:absolute;top:0;height:79px;line-height:79px;text-align:center;white-space:nowrap}
.mainnav a.active{background:var(--blue);color:var(--white)}

.pagebar{position:absolute;left:0;top:108px;width:1150px;height:58px;background:var(--band)}
.pagebar h1{position:absolute;left:155px;top:15px;font-size:10px;font-weight:700;color:var(--ink)}
.pagebar .crumbs{position:absolute;left:155px;top:33px;font-size:9.5px;color:var(--ink)}

.sidenav{position:absolute;left:155px;top:209px;width:194px}
.sidenav h2{font-size:10px;font-weight:700;color:var(--ink);padding-bottom:6px;border-bottom:1px solid var(--rule)}
.sidenav ul{list-style:none;padding-left:14px;margin-top:3px}
.sidenav li{font-size:9.5px;line-height:21.6px;color:var(--ink)}
.sidenav li.current{color:var(--blue);font-weight:600}

.content{position:absolute;left:370px;top:207px;width:410px}
.content h2{font-size:12.5px;font-weight:600;color:var(--ink);padding-bottom:5px;border-bottom:1px solid var(--rule);margin-bottom:19px;letter-spacing:.3px}
.content p{font-size:9.2px;line-height:14.4px;text-align:justify;color:var(--text)}
.content .intro{margin-bottom:10px}
.policy{padding-left:15px}
.policy h3{font-size:10px;line-height:14.4px;font-weight:600;color:var(--ink);margin-bottom:10.6px}
.policy p{margin-bottom:9.4px}

.widget{position:absolute;left:802px;width:192px;border:1px solid var(--rule);overflow:hidden}
.widget h3{height:32px;line-height:32px;background:var(--blue);color:var(--white);font-size:10px;font-weight:700;padding-left:12px;margin:-1px -1px 0}
.widget .body{padding:9px 6px 0 13px;font-size:9px;color:var(--ink)}
.widget dd,.widget dt{white-space:nowrap}
.hours{top:200px;height:208px}
.hours .lead{line-height:13px;margin-bottom:6px;padding-right:8px}
.hours dl{display:grid;grid-template-columns:86px auto;line-height:17.2px}
.contact{top:430px;height:143px}
.contact dl{display:grid;grid-template-columns:90px auto;line-height:14.4px;padding-top:2px}

.footer{position:absolute;left:0;top:982px;width:1150px;height:218px;background:var(--footer);border-top:4px solid var(--blue)}
.footer .brand{top:52px;color:var(--white)}
.footer .about{position:absolute;left:155px;top:86px;width:200px;font-size:8.4px;line-height:12.8px;color:#bdbdbd}
.fcol{position:absolute;top:34px;font-size:9.3px;color:var(--footer-text)}
.fcol h4{font-size:11.5px;font-weight:600;color:var(--footer-head);margin-bottom:6px}
.fcol li{list-style:none;line-height:17.2px}
.fcol li.on{color:#d8d8d8}
.fcol dl{display:grid;grid-template-columns:85px auto;line-height:14.4px}
.fcol dd{white-space:nowrap}
.fbottom{position:absolute;left:0;top:184px;width:1150px;border-top:1px solid #444;font-size:9.3px;color:#7a7a7a}
.fbottom .copy{position:absolute;left:155px;top:9px}
.fbottom .legal{position:absolute;left:443px;top:9px}
.fbottom .legal a{margin-right:22px}
</style>
</head>
<body>

<div class="topbar">
  <div class="help"><span>To help Here : 111 222 4848</span><span>Email : Contact@ Brevacare.ca</span></div>
  <div class="quick"><a href="#">Book an Appointment</a><a href="#">Physician Toolbox</a></div>
</div>

<header class="header">
  <div class="brand"><span class="dot"></span>Brevacare Clinics</div>
  <nav class="mainnav">
    <a href="#" style="left:530px;width:60px">Home</a>
    <a href="#" class="active" style="left:606px;width:57px">Our Clinic</a>
    <a href="#" style="left:680px;width:72px">Our Staff</a>
    <a href="#" style="left:766px;width:64px">Resources</a>
    <a href="#" style="left:848px;width:50px">Alerts</a>
    <a href="#" style="left:913px;width:70px">Contact Us</a>
  </nav>
</header>

<section class="pagebar">
  <h1>POLICES</h1>
  <div class="crumbs">HOME / OUR CLINIC / POLICES</div>
</section>

<aside class="sidenav">
  <h2>OUR CLINIC</h2>
  <ul>
    <li>About</li>
    <li>Misssion</li>
    <li>Services</li>
    <li class="current">Policies</li>
    <li>Schedules</li>
  </ul>
</aside>

<main class="content">
  <h2>POLICIES</h2>
  <p class="intro">Lorem Ipsum is simply dummy text of the printing and typesetting industry. Lorem Ipsum has been the industry's standard dummy text ever since the 1500s, when an unknown printer took a galley of type and scrambled it to make a type specimen book. It has survived not only five centuries, but also the leap into electronic typesetting, remaining essentially unchanged.</p>
  <div class="policy"><h3>Late arrivals</h3><p>Lorem Ipsum is simply dummy text of the printing and typesetting industry. Lorem Ipsum has been the industry's standard dummy text ever since the 1500s, when an unknown printer took a galley of type and scrambled it to make a type specimen book. It has survived not only five centuries, but also the leap into electronic typesetting, remaining essentially unchanged.</p></div>
  <div class="policy"><h3>Missed appointments</h3><p>Lorem Ipsum is simply dummy text of the printing and typesetting industry. Lorem Ipsum has been the industry's standard dummy text ever since the 1500s, when an unknown printer took a galley of type and scrambled it to make a type specimen book. It has survived not only five centuries, but also the leap into electronic typesetting, remaining essentially unchanged.</p></div>
  <div class="policy"><h3>Fees for missed appointments</h3><p>Lorem Ipsum is simply dummy text of the printing and typesetting industry. Lorem Ipsum has been the industry's standard dummy text ever since the 1500s, when an unknown printer took a galley of type and scrambled it to make a type specimen book. It has survived not only five centuries, but also the leap into electronic typesetting, remaining essentially unchanged.</p></div>
  <div class="policy"><h3>Referrals and follow-ups</h3><p>Lorem Ipsum is simply dummy text of the printing and typesetting industry. Lorem Ipsum has been the industry's standard dummy text ever since the 1500s, when an unknown printer took a galley of type and scrambled it to make a type specimen book. It has survived not only five centuries, but also the leap into electronic typesetting, remaining essentially unchanged.</p></div>
  <div class="policy"><h3>Services not covered by RDA</h3><p>Lorem Ipsum is simply dummy text of the printing and typesetting industry. Lorem Ipsum has been the industry's standard dummy text ever since the 1500s, when an unknown printer took a galley of type and scrambled it to make a type specimen book. It has survived not only five centuries, but also the leap into electronic typesetting, remaining essentially unchanged.</p></div>
  <div class="policy"><h3>Information for LTF patients</h3><p>Lorem Ipsum is simply dummy text of the printing and typesetting industry. Lorem Ipsum has been the industry's standard dummy text ever since the 1500s, when an unknown printer took a galley of type and scrambled it to make a type specimen book. It has survived not only five centuries, but also the leap into electronic typesetting, remaining essentially unchanged.</p></div>
</main>

<section class="widget hours">
  <h3>HOURS OF OPRATION</h3>
  <div class="body">
    <p class="lead">Lorem Ipsum is simply dummy text of the printing and typesetting</p>
    <dl>
      <dt>Monday :</dt><dd>8:00 AM - 6:00 PM</dd>
      <dt>Tuesday :</dt><dd>8:00 AM - 6:00 PM</dd>
      <dt>Wednessday :</dt><dd>8:00 AM - 6:00 PM</dd>
      <dt>Thursday :</dt><dd>8:00 AM - 6:00 PM</dd>
      <dt>Friday :</dt><dd>8:00 AM - 6:00 PM</dd>
      <dt>Saturday :</dt><dd>9:00 AM - 4:00 PM</dd>
      <dt>Sunday :</dt><dd>9:00 AM - 4:00 PM</dd>
    </dl>
  </div>
</section>

<section class="widget contact">
  <h3>CONTACT INFO</h3>
  <div class="body">
    <dl>
      <dt>Telephone :</dt><dd>604-555-0199</dd>
      <dt>Email:</dt><dd>info@brevacare.ca</dd>
      <dt>Address:</dt><dd>48 Alder Lane<br>Kelsworth,B.<br>Canada, V2K 4RT</dd>
    </dl>
  </div>
</section>

<footer class="footer">
  <div class="brand">Brevacare Clinics</div>
  <p class="about">Lorem Ipsum is simply dummy text of the printing and typesetting industry. Lorem Ipsum has been the industry's standard dummy text</p>
  <div class="fcol" style="left:442px">
    <h4>Navigation</h4>
    <ul><li class="on">Home</li><li>Our Clinic</li><li>Newsletter</li><li>Our Staff</li><li>Resources</li></ul>
  </div>
  <div class="fcol" style="left:657px">
    <h4>Links</h4>
    <ul><li>Help</li><li>Support</li><li>Privacy Policy</li></ul>
  </div>
  <div class="fcol" style="left:801px;width:200px">
    <h4>Contact Us</h4>
    <dl>
      <dt>Telephone :</dt><dd>604-555-0199</dd>
      <dt>Email:</dt><dd>info@brevacare.ca</dd>
      <dt>Address:</dt><dd>48 Alder Lane<br>Kelsworth,B. Canada,<br>V2K 4RT</dd>
    </dl>
  </div>
  <div class="fbottom">
    <span class="copy">© 2015 Brevacare Clinics. All Rights Reservsd</span>
    <span class="legal"><a href="#">About Us</a><a href="#">Terms of Use</a><a href="#">Privacy Policy</a></span>
  </div>
</footer>

</body>
</html>
```